New Interrior Decoration company needs new website

We need a website for our new company specialising in interior decoration to residential and commercial markets.
We supply and install decorative and printed films for office and home decoration such as feature walls.
We would like to keep the design simple and clean.

Target Market(s)

Architects and interior designaers

Industry/Entity Type

It Company

Number of Pages Required

5+ page

Font styles to use
Sans Serif

Requirements
Must have
• Home page,
• Services/products page (split into commercial and residential)
• Gallery (split into commercial and residential)
• contact form and page
Nice to have
• Very clean and minimalistic design.

```html
<!DOCTYPE html>
<html lang="en">
<head>
<meta charset="utf-8">
<title>Example Interiors</title>
<link rel="stylesheet" href="https://fonts.googleapis.com/css2?family=Roboto:wght@300;400;500;700&display=swap">
<style>
:root{
  --blue:#0c5cc2;
  --white:#ffffff;
  --ink:#5c5f66;
  --muted:#8a8d93;
  --line:#d9dbde;
  --band:#2b2c31;
  --band-light:#33353a;
  --footer:#232529;
  --footer-text:#8d9096;
  --hero-shade:rgba(28,28,30,.78);
}
*{box-sizing:border-box;margin:0;padding:0}
html,body{width:839px;height:1200px;overflow:hidden}
body{font-family:"Roboto",sans-serif;background:var(--white);position:relative;color:var(--ink)}
.hero{position:absolute;left:0;top:0;width:839px;height:442px;overflow:hidden}
.hero-photo{position:absolute;inset:0;background:
  radial-gradient(ellipse at 70% 30%,#b9b6b0 0%,transparent 55%),
  linear-gradient(90deg,#6d655c 0%,#8f8a84 30%,#a6a6a4 60%,#7d7f82 100%)}
.hero-photo::after{content:"";position:absolute;inset:0;background:rgba(40,40,40,.25)}
.main-nav{position:absolute;left:67px;top:33px;display:flex}
.main-nav a{color:var(--white);text-decoration:none;font-size:13.5px;font-weight:500;margin-right:23px}
.brand{position:absolute;display:flex;align-items:center;gap:5px;font-weight:700;text-transform:uppercase;letter-spacing:-.4px}
.brand-mark{background:var(--blue);display:block}
.hero .brand{left:319px;top:103px;font-size:20px;color:#2e3138;line-height:.95}
.hero .brand .brand-mark{width:40px;height:36px}
.hero-title{position:absolute;left:0;width:839px;top:195px;text-align:center;color:var(--white);font-size:26px;font-weight:700}
.hero-sub{position:absolute;left:0;width:839px;top:230px;text-align:center;color:var(--white);font-size:14.5px;letter-spacing:.3px}
.quote-band{position:absolute;left:0;top:369px;width:839px;height:73px;background:var(--hero-shade)}
.quote-input{position:absolute;left:273px;top:16px;width:195px;height:32px;border:1px solid #5e6066;border-right:none;border-radius:3px 0 0 3px;color:#cfd0d3;font-size:9.5px;padding-left:16px;line-height:30px}
.quote-btn{position:absolute;left:467px;top:16px;width:89px;height:32px;background:var(--blue);color:var(--white);font-size:12px;font-weight:500;text-align:center;line-height:32px;border-radius:0 3px 3px 0}
.contact-title{position:absolute;left:0;width:839px;top:467px;text-align:center;color:var(--blue);font-size:20.5px;font-weight:300}
.contact-lead{position:absolute;left:0;width:839px;top:499px;text-align:center;color:var(--muted);font-size:11px;font-weight:300;line-height:15.5px}
.direct{position:absolute;left:189px;top:563px;line-height:1}
.direct h3{color:var(--blue);font-size:10.5px;font-weight:500;margin-bottom:9px}
.direct dt{color:var(--muted);font-size:9px;margin-bottom:4px}
.direct dd{color:#55585e;font-size:10px;font-weight:500;margin-bottom:13px}
.field{position:absolute;left:413px;width:236px;border:1px solid var(--line);color:#6f7278;font-size:10.5px;padding-left:18px}
.field-name{top:561px;height:32px;line-height:31px}
.field-email{top:604px;height:32px;line-height:31px}
.field-message{top:647px;height:168px;padding-top:10px}
.send-btn{position:absolute;left:542px;top:836px;width:108px;height:27px;background:var(--blue);border-radius:3px;color:var(--white);font-size:9.5px;font-weight:500;display:flex;align-items:center;gap:6px;padding-left:10px}
.offer-band{position:absolute;left:0;top:911px;width:839px;height:67px;background:var(--band);overflow:hidden}
.offer-band svg{position:absolute;left:0;top:0}
.offer-text{position:absolute;left:207px;top:20px;color:var(--white);font-size:19.5px;font-weight:300;letter-spacing:-.2px}
.offer-btn{position:absolute;left:544px;top:15px;width:100px;height:33px;background:var(--blue);color:var(--white);font-size:12.5px;font-weight:500;text-align:center;line-height:33px;border-radius:2px}
.site-footer{position:absolute;left:0;top:978px;width:839px;height:222px;background:var(--footer)}
.site-footer .brand{left:103px;top:30px;font-size:14.5px;color:#dfe0e2;line-height:.95}
.site-footer .brand .brand-mark{width:36px;height:23px}
.footer-about{position:absolute;left:103px;top:67px;width:282px;color:var(--footer-text);font-size:8.6px;line-height:12.5px}
.copyright{position:absolute;left:103px;top:132px;color:var(--footer-text);font-size:8px}
.footer-col{position:absolute;top:37px}
.footer-col h4{color:var(--white);font-size:10px;font-weight:500;margin-bottom:8px}
.footer-col p{color:#6f7278;font-size:9px;line-height:15px}
.col-contact{left:483px}
.col-follow{left:643px}
.social{display:flex;gap:11px;margin-top:-1px}
.social span{width:9px;height:9px;background:#b9bbbf;border-radius:2px;display:block}
.footer-rule{position:absolute;left:103px;top:172px;width:633px;height:1px;background:#34363b}
.payments{position:absolute;left:103px;top:190px;display:flex;gap:14px;align-items:center}
.payments span{display:block;height:14px;background:#4a4c52;border-radius:3px}
.to-top{position:absolute;left:686px;top:184px;display:flex;align-items:center;gap:12px;color:#c9cbce;font-size:9.5px}
.to-top svg{display:block}
</style>
</head>
<body>
<header class="hero">
  <div class="hero-photo" role="img" aria-label="Photograph of a modern interior with a white dining table, dark chairs, pendant lights and a kitchen island"></div>
  <nav class="main-nav">
    <a href="#">About</a><a href="#">Services</a><a href="#">Gallery</a><a href="#">Contact</a>
  </nav>
  <div class="brand"><span class="brand-mark"></span><span>Example<br>Interiors</span></div>
  <h1 class="hero-title">Stylish, Innovative Workmanship</h1>
  <p class="hero-sub">SYMBOL OF EXTRAORDINARY SPACE AND GREAT DESIGN</p>
  <div class="quote-band">
    <div class="quote-input">Enter your e-mail here</div>
    <div class="quote-btn">Quote Today</div>
  </div>
</header>

<section class="contact">
  <h2 class="contact-title">We Would Love to Hear from You</h2>
  <p class="contact-lead">Drop us a line with your queries, quote demands or just to say hi<br>Looking forward to hearing from you</p>
  <div class="direct">
    <h3>You can &nbsp;also reach us directly</h3>
    <dl>
      <dt>Email:</dt><dd>info@example.com</dd>
      <dt>Phone:</dt><dd>02 5550 0142</dd>
    </dl>
  </div>
  <div class="field field-name">Enter your name here</div>
  <div class="field field-email">Enter Your email here</div>
  <div class="field field-message">Your Message here</div>
  <div class="send-btn">
    <svg width="15" height="12" viewBox="0 0 15 12"><rect x="0.75" y="0.75" width="13.5" height="10.5" fill="none" stroke="#fff" stroke-width="1.2"/><path d="M1 1l6.5 5.5L14 1M1 11l4.5-4.5M14 11L9.5 6.5" fill="none" stroke="#fff" stroke-width="1.1"/></svg>
    Send Message
  </div>
</section>

<section class="offer-band">
  <svg width="839" height="67"><polygon points="480,0 839,0 839,67 498,67" fill="var(--band-light)"/></svg>
  <p class="offer-text">Take a look at all what we offer you</p>
  <div class="offer-btn">Check it Out</div>
</section>

<footer class="site-footer">
  <div class="brand"><span class="brand-mark"></span><span>Example<br>Interiors</span></div>
  <p class="footer-about">The Example Interiors team have over 20 years experience in the design, building, vinyl application and signage trades, giving us the ability to work through any creative or architectural needs your project may require.</p>
  <p class="copyright">© 2016 &nbsp;Example Interiors All rights reserved</p>
  <div class="footer-col col-contact">
    <h4>Contact Us</h4>
    <p>info@example.com<br>02 5550 0142</p>
  </div>
  <div class="footer-col col-follow">
    <h4>Follow Us</h4>
    <div class="social"><span></span><span></span><span></span><span></span></div>
  </div>
  <div class="footer-rule"></div>
  <div class="payments">
    <span style="width:28px"></span><span style="width:27px"></span><span style="width:27px"></span><span style="width:38px"></span><span style="width:18px"></span><span style="width:32px"></span>
  </div>
  <div class="to-top">Top
    <svg width="25" height="25" viewBox="0 0 25 25"><circle cx="12.5" cy="12.5" r="11.8" fill="none" stroke="#c9cbce" stroke-width="1"/><path d="M9.5 14l3-3 3 3" fill="none" stroke="#e3e4e6" stroke-width="1.3"/></svg>
  </div>
</footer>
</body>
</html>
```